Heron Loan Partners Business Card

We need a business card design for our mortgage servicing company. In addition to servicing the loans of homeowners, we help homeowners with purchasing their homes and any mortgage refinancing. We would like to see designs that use the colors in the logo attached below (gold-ish yellow and navy blue), and any other design you deem fit! The design should communicate a simpler life with smart mortgages provided by Heron.

```html
<!DOCTYPE html>
<html lang="en">
<head>
<meta charset="utf-8">
<title>Heron Loan Partners – Business Card</title>
<link rel="stylesheet" href="https://fonts.googleapis.com/css2?family=Libre+Baskerville:wght@700&family=Montserrat:wght@400;600&display=swap">
<style>
  :root {
    --backdrop: #d3d4d6;
    --card: #ffffff;
    --gold: #dcae3e;
    --navy: #221f4a;
    --teal: #2aa6a0;
  }
  * { margin: 0; padding: 0; box-sizing: border-box; }
  html, body { width: 900px; height: 1200px; overflow: hidden; }
  body {
    background: var(--backdrop);
    font-family: "Montserrat", sans-serif;
    color: var(--navy);
    position: relative;
  }
  .card {
    position: absolute;
    left: 135px;
    width: 630px;
    height: 360px;
    background: var(--card);
  }
  .card--front { top: 213px; }
  .card--back { top: 627px; }

  .brand-name {
    position: absolute;
    left: 0; right: 0;
    text-align: center;
    font-family: "Montserrat", sans-serif;
    font-weight: 600;
    font-size: 34px;
    letter-spacing: 0.5px;
    color: var(--gold);
  }
  .card--front .brand-name { top: 162px; }
  .card--back .brand-name { top: 80px; font-size: 30px; }

  .person {
    position: absolute;
    right: 329px;
    top: 198px;
    text-align: right;
  }
  .person__name {
    font-family: "Libre Baskerville", serif;
    font-weight: 700;
    font-size: 21px;
    color: var(--gold);
    white-space: nowrap;
  }
  .person__title {
    font-size: 14px;
    letter-spacing: 1px;
    margin-top: 6px;
  }
  .divider {
    position: absolute;
    left: 315px;
    top: 190px;
    width: 2px;
    height: 70px;
    background: var(--teal);
  }
  .contacts {
    position: absolute;
    left: 326px;
    top: 191px;
    list-style: none;
  }
  .contacts li {
    display: flex;
    align-items: center;
    height: 23.5px;
    font-size: 14px;
    letter-spacing: 0.6px;
    white-space: nowrap;
  }
  .contacts li.phone { letter-spacing: 2.4px; }
  .contacts svg { width: 11px; height: 11px; margin-right: 8px; flex: none; }
  .address {
    position: absolute;
    left: 0; right: 0;
    top: 279px;
    text-align: center;
    font-size: 14px;
    letter-spacing: 0.5px;
  }
  .address svg { display: block; margin: 0 auto 10px; width: 11px; height: 15px; }
</style>
</head>
<body>
  <section class="card card--front">
    <div class="brand-name">Heron Loan Partners</div>
  </section>

  <section class="card card--back">
    <div class="brand-name">Heron Loan Partners</div>

    <div class="person">
      <div class="person__name">Dana Whitfield</div>
      <div class="person__title">Founder</div>
    </div>
    <div class="divider"></div>
    <ul class="contacts">
      <li class="phone">
        <svg viewBox="0 0 12 12"><path fill="var(--gold)" d="M2.5 0.5l2 2.3-1 1.3c.8 1.6 2 2.8 3.6 3.6l1.3-1 2.3 2-1.2 2.3C5 10.6 1.4 7 .5 1.7z"/></svg>
        (888)-555-0142
      </li>
      <li>
        <svg viewBox="0 0 12 12"><rect x="0.5" y="2.5" width="11" height="7.5" fill="var(--gold)"/><path d="M0.8 2.8L6 7l5.2-4.2" fill="none" stroke="#fff" stroke-width="1"/></svg>
        info@heronloan.com
      </li>
      <li>
        <svg viewBox="0 0 12 12"><circle cx="6" cy="6" r="5" fill="none" stroke="var(--gold)" stroke-width="1.4"/><path d="M1 6h10M6 1c-2.5 3-2.5 7 0 10M6 1c2.5 3 2.5 7 0 10" fill="none" stroke="var(--gold)" stroke-width="1"/></svg>
        www.heronloan.com
      </li>
    </ul>

    <div class="address">
      <svg viewBox="0 0 11 15"><path fill="var(--gold)" d="M5.5 0A5.5 5.5 0 0 0 0 5.5C0 9.5 5.5 15 5.5 15S11 9.5 11 5.5A5.5 5.5 0 0 0 5.5 0zm0 7.8a2.3 2.3 0 1 1 0-4.6 2.3 2.3 0 0 1 0 4.6z"/></svg>
      218 Bayview Ave S, Clearwater, FL 33756
    </div>
  </section>
</body>
</html>
```